AMBER AND SLATE WEB

We need a home design in wordpress, we have now a web but we would like to improve it. Our current web is www.amberandslatevillas.example Our business is holliday rental of villas in Ibiza. Our guest must know that we are a reliable company, professional and with experience and good reviews. We want them to click in our reservation engine: https://bookings.amberandslatevillas.example/en/ and make reservation in our website. We would also like to say that all the properties that we have are just us who commercialize so we have best price available. Many people are going to see our villas in staylist.example and look to our website to make a reservation with us so we need to show them that they are at the right place and click at our link to our reservation engine. What make us special is that we are a local company, we are from Ibiza, Our guests are always received in person by the Amber and Slate Ibiza team. You will enjoy extensive tourist information when you check in and during the entire stay. You will be attended by ChatterLine and calls, always happy to help so that you have a happy and fun stay! Our guest stay is better than in hotel as they have more spece, private swiming pool, private garden, barbeque ... To rent a villa is the best way to stay in Ibiza. We also have a promotional video: https://vidshare.example/Qm7TzR2pLxA Let our philosophy be shown, we think that coming on holiday to Ibiza implies seeing the nature that we have in Ibiza, hence our name AMBER AND SLATE, like the pins that almost touch the sea in Ibiza, or the posidonea meadows where the intense green of the seaweed and the blue of the sea. We are aware of the environment, and we love Ibiza. For us, the client who visits Ibiza, should rent a car, go around the island, eat in a restaurant one day in front of the sea, is a night of partying to the discs, go shopping, visit the ancient heritage of Umanity, make some aquatic sport, enjoy the pool, those are for us Ibiza.

Target Market(s)

Europe, people from Holand, UK, Germany, France, Spain ...

Industry/Entity Type

Tourism

Colors

Designer to choose colors to be used in the design.

Requirements
Must have
• Pictures of Ibiza.
Nice to have
• Our name Amber and Slate Ibiza is beacuse in Ibiza there is forest that almost touch the watter of the Mediterranean sea, so you can see green of the forest and blue of the sea and the sky. And also beacause under the watter of the sea there is a plant called Posidonia that is also green please see the picture of posidonia.

```html
<!DOCTYPE html>
<html lang="en">
<head>
<meta charset="utf-8">
<title>Amber and Slate Villas Ibiza</title>
<link href="https://fonts.googleapis.com/css2?family=Alegreya:wght@400;500&family=Open+Sans:wght@400;600&display=swap" rel="stylesheet">
<style>
:root{
  --green:#8aab2c;
  --green-dark:#6f8c1f;
  --blue:#2f86c7;
  --link-blue:#1d56a3;
  --text:#3a3a3a;
  --muted:#6b6b6b;
  --tile:#e6e6e6;
  --band:#ebebeb;
  --footer:#1d1d1d;
  --white:#ffffff;
}
*{margin:0;padding:0;box-sizing:border-box}
html,body{width:1200px;height:4104px;overflow:hidden;background:var(--white)}
body{font-family:"Open Sans",Arial,sans-serif;color:var(--text);position:relative}
.page{position:relative;width:1200px;height:4104px;overflow:hidden}
.abs{position:absolute}
.serif{font-family:"Alegreya",Georgia,serif}
.btn{position:absolute;background:var(--green);color:var(--white);font-weight:600;font-size:15px;display:flex;align-items:center;justify-content:center;border-radius:2px}

/* header */
.brand{left:145px;top:40px;height:40px;display:flex;align-items:center;gap:12px}
.brand-mark{width:28px;height:28px;background:var(--text)}
.brand-name{font-family:"Open Sans",Arial,sans-serif;font-weight:600;color:var(--text);font-size:22px;line-height:1}
.lang{left:822px;top:16px;width:123px;height:39px;background:#e3e3e3;border-radius:3px;font-size:14px;color:#555;display:flex;align-items:center;padding-left:14px;gap:8px}
.lang .flag{width:18px;height:12px;background:#2a4b8d}
.lang .caret{margin-left:auto;margin-right:12px;font-size:10px}
.book{left:955px;top:16px;width:100px;height:39px}
.nav{right:144px;top:87px;display:flex;gap:33px;font-size:13px;color:#555}
.nav .active{color:var(--link-blue)}

/* hero */
.hero{left:0;top:120px;width:1200px;height:500px;background:linear-gradient(160deg,#1b2e9c 0%,#1a3bb0 40%,#2453c2 65%,#163a8a 100%)}
.hero-title{left:0;top:255px;width:1200px;text-align:center;color:var(--white);font-size:41px}
.field-label{top:328px;color:var(--white);font-size:13px}
.field{top:351px;height:39px;background:var(--white);font-size:11px;color:#444;display:flex;align-items:center;padding:0 10px;border-radius:2px}
.field .ico{margin-left:auto;width:13px;height:11px;background:#666;border-radius:2px}
.search{left:879px;top:351px;width:176px;height:39px;color:#333;text-transform:uppercase}
.hero-arrow{top:313px;width:22px;height:28px}

/* intro */
.intro-title{left:143px;top:688px;font-size:33px;line-height:41px;color:var(--green)}
.intro-text{left:143px;top:778px;width:607px;font-size:12.3px;line-height:21px}
.intro-text p{margin-bottom:21px}
.intro-photo{left:771px;top:695px;width:285px;height:372px;background:linear-gradient(180deg,#3d6fb3 0%,#8fb3d6 35%,#5c7d3a 70%,#3d5c22 100%)}

/* video band */
.video-band{left:0;top:1148px;width:1200px;height:480px;background:linear-gradient(180deg,#3c3d39 0%,#5a5b55 45%,#3e4a4a 100%)}
.play{left:577px;top:1317px;width:46px;height:46px;border-radius:50%;background:var(--white)}
.video-title{left:0;top:1368px;width:1200px;text-align:center;color:var(--white);font-size:32px}
.watch{left:534px;top:1418px;width:132px;height:40px;color:#222}

/* activities */
.section-title{left:0;width:1200px;text-align:center;color:var(--green);font-size:33px}
.tile{width:219px;height:144px;background:var(--tile);display:flex;flex-direction:column;align-items:center;padding:30px 22px 0;font-size:15px;color:#333;text-align:center;line-height:21px}
.tile svg{width:44px;height:44px;margin-bottom:6px;fill:#333;flex:none}

/* philosophy */
.philo-band{left:0;top:2147px;width:1200px;height:480px;background:linear-gradient(180deg,#4c5f75 0%,#6d8397 30%,#2e8098 52%,#237a8b 75%,#1d6a7b 100%)}
.philo-title{left:0;top:2323px;width:1200px;text-align:center;color:var(--white);font-size:33px}
.philo-text{left:145px;top:2374px;width:910px;text-align:center;color:var(--white);font-size:13px;line-height:24px}

/* experiences */
.exp-photo{left:143px;top:2753px;width:457px;height:280px;background:linear-gradient(135deg,#4d6b2f 0%,#8aa25a 45%,#c9b79a 70%,#6d7b4a 100%)}
.exp-play{left:350px;top:2872px;width:44px;height:44px;border-radius:50%;background:var(--white)}
.exp-panel{left:600px;top:2753px;width:456px;height:280px;background:#dcdcdc}
.exp-quote{left:630px;top:2793px;width:395px;font-size:11px;line-height:19px;color:#444}
.exp-ref{left:630px;top:2893px;font-size:14px;color:var(--link-blue)}
.avatar{left:636px;top:2934px;width:54px;height:54px;border-radius:50%;background:#8a8f96}
.exp-name{left:636px;top:2992px;width:54px;text-align:center;font-size:11px;color:#666}
.quote-mark{left:948px;top:2935px;width:92px;height:80px}
.exp-arrow{top:2880px;width:22px;height:28px}

/* properties */
.props-band{left:0;top:3113px;width:1200px;height:560px;background:var(--band)}
.prop-photo{top:3246px;width:298px;height:192px}
.prop-name{top:3448px;font-size:16px;color:var(--link-blue)}
.prop-meta{top:3477px;font-size:13px;color:#333;display:flex;gap:24px}
.prop-note{top:3500px;font-size:10px;line-height:16px;color:#555}
.view-all{left:534px;top:3555px;width:132px;height:37px;color:#222}

/* newsletter */
.email{left:446px;top:3800px;width:219px;height:38px;background:#e6e6e6;font-size:10px;color:#555;display:flex;align-items:center;padding-left:16px}
.submit{left:665px;top:3800px;width:89px;height:38px;color:#222}

/* footer */
.foot-links{left:145px;top:4024px;font-size:11px;color:#aaa;display:flex;gap:9px}
.copyright{left:145px;top:4052px;font-size:11px;color:#aaa}
.socials{left:928px;top:4046px;display:flex;gap:20px}
.socials span{width:16px;height:16px;border-radius:50%;background:#9a9a9a}
</style>
</head>
<body>
<div class="page">

  <!-- header -->
  <div class="abs brand">
    <div class="brand-mark"></div>
    <div class="brand-name">Amber and Slate</div>
  </div>
  <div class="abs lang"><span class="flag"></span>English<span class="caret">&#9662;</span></div>
  <div class="btn book">Book Now</div>
  <nav class="abs nav">
    <span class="active">Home</span><span>All Properties</span><span>Experience</span><span>About us</span><span>Contact Us</span>
  </nav>

  <!-- hero -->
  <div class="abs hero" role="img" aria-label="Photo of an Ibiza cove with boats, pine forest and clear blue sea"></div>
  <h1 class="abs hero-title serif" style="font-weight:400">The best way to stay in Ibiza!</h1>
  <svg class="abs hero-arrow" style="left:52px" viewBox="0 0 22 28"><path d="M15 4 L6 14 L15 24" stroke="#fff" stroke-width="3" fill="none"/></svg>
  <svg class="abs hero-arrow" style="left:1125px" viewBox="0 0 22 28"><path d="M7 4 L16 14 L7 24" stroke="#fff" stroke-width="3" fill="none"/></svg>

  <div class="abs field-label" style="left:143px">Date of entry and exit</div>
  <div class="abs field-label" style="left:433px">Nights</div>
  <div class="abs field-label" style="left:538px">No. of people and rooms</div>
  <div class="abs field-label" style="left:772px">Promo Code</div>
  <div class="abs field" style="left:145px;width:273px">Select the dates of your stay<span class="ico"></span></div>
  <div class="abs field" style="left:435px;width:88px">1<span style="margin-left:auto;font-size:9px">&#9660;</span></div>
  <div class="abs field" style="left:540px;width:217px">2 adults (1 room)<span class="ico"></span></div>
  <div class="abs field" style="left:773px;width:90px">Promo<span class="ico"></span></div>
  <div class="btn search">Search</div>

  <svg class="abs" style="left:0;top:500px" width="1200" height="125" viewBox="0 0 1200 125">
    <defs>
      <linearGradient id="heroWave" x1="0" x2="1" y1="0" y2="0">
        <stop offset="0" stop-color="#6b9a2a"/>
        <stop offset="0.5" stop-color="#3a9a7a"/>
        <stop offset="1" stop-color="#2f86c7"/>
      </linearGradient>
    </defs>
    <path d="M0 38 Q420 140 820 48 Q1000 10 1200 100 L1200 125 L0 125Z" fill="url(#heroWave)"/>
    <path d="M0 58 Q400 150 800 66 Q1000 28 1200 110 L1200 125 L0 125Z" fill="#fff"/>
  </svg>

  <!-- intro -->
  <h2 class="abs intro-title serif" style="font-weight:400">VILLAS AND THE COUNTRYSIDE<br>The best option to stay in Ibiza</h2>
  <div class="abs intro-text">
    <p>Amber and Slate Villas Ibiza is a company specialized in offering its clients accommodation in Villas on the countryside of Ibiza. Our guests enjoy the rural Ibiza, tranquility, relax, private pool, close to dream beaches and coves, the best restaurants, an unforgettable holiday for family or friends.</p>
    <p>Every day can be a different experience, beach, restaurant, flea market, disco, hiking, kayaking, horseback riding, shopping, history, boat ride! There is a lot of variety for all budgets!</p>
    <p>The maximum distances of the island are 41 kilometers from north to south and 15 kilometers from east to west, we always recommend renting a car. Enjoy the freedom to go where you prefer, without depending on schedules or public transportation.</p>
    <p>Each client is different, both for those who discover Ibiza for the first time and for those who have already been many times, it is a pleasure for us to share our favorite places with our guests and help them to make their experience very special.</p>
  </div>
  <div class="abs intro-photo" role="img" aria-label="Photo of sun loungers under a parasol on a garden lawn with a valley view"></div>

  <!-- video -->
  <div class="abs video-band" role="img" aria-label="Still from the promotional video: a woman by a calm bay at dusk"></div>
  <div class="abs play"></div>
  <svg class="abs" style="left:593px;top:1330px" width="18" height="20" viewBox="0 0 18 20"><path d="M2 1 L17 10 L2 19Z" fill="#222"/></svg>
  <h2 class="abs video-title serif" style="font-weight:400">Have you ever seen this face of Ibiza?</h2>
  <div class="btn watch">WATCH THIS!</div>

  <!-- activities -->
  <h2 class="abs section-title serif" style="top:1700px;font-weight:400">Pellentesque imperdiet dolor</h2>

  <div class="abs tile" style="left:143px;top:1763px">
    <svg viewBox="0 0 44 44"><path d="M8 22 L12 12 H32 L36 22 H40 V32 H36 V36 H30 V32 H14 V36 H8 V32 H4 V22Z M14 15 L11 22 H33 L30 15Z"/><circle cx="11" cy="27" r="2.5" fill="#e6e6e6"/><circle cx="33" cy="27" r="2.5" fill="#e6e6e6"/></svg>
    Should rent a car</div>
  <div class="abs tile" style="left:375px;top:1763px">
    <svg viewBox="0 0 44 44"><path d="M20 14 Q14 8 8 12 Q14 10 18 15 Q10 16 8 22 Q14 17 20 17 L18 36 H23 L22 17 Q28 17 34 22 Q32 16 24 15 Q28 10 34 12 Q28 8 22 14Z"/><rect x="8" y="36" width="30" height="4"/></svg>
    Go around the island</div>
  <div class="abs tile" style="left:606px;top:1763px">
    <svg viewBox="0 0 44 44"><rect x="3" y="6" width="2" height="12"/><rect x="7" y="6" width="2" height="12"/><rect x="3" y="16" width="6" height="4"/><rect x="5" y="18" width="2" height="20"/><circle cx="24" cy="22" r="12"/><circle cx="24" cy="22" r="7" fill="#e6e6e6"/><path d="M38 6 Q42 14 40 22 H38 V38 H36 V6Z"/></svg>
    Eat in a restaurant one day in front of the sea</div>
  <div class="abs tile" style="left:837px;top:1763px">
    <svg viewBox="0 0 44 44"><rect x="21" y="4" width="2" height="10"/><circle cx="22" cy="26" r="11"/><path d="M11 26 H33 M22 15 V37 M14 19 H30 M14 33 H30" stroke="#e6e6e6" stroke-width="1.5"/></svg>
    Night of partying to the discos</div>

  <div class="abs tile" style="left:143px;top:1923px">
    <svg viewBox="0 0 44 44"><path d="M2 8 H8 L14 30 H36 L40 14 H11" stroke="#333" stroke-width="3" fill="none"/><path d="M13 18 H38 M14 23 H37" stroke="#333" stroke-width="2"/><circle cx="16" cy="36" r="3"/><circle cx="33" cy="36" r="3"/></svg>
    Go shopping</div>
  <div class="abs tile" style="left:375px;top:1923px">
    <svg viewBox="0 0 44 44"><rect x="17" y="3" width="10" height="5"/><path d="M15 9 H29 Q34 14 32 20 Q36 28 30 36 V40 H14 V36 Q8 28 12 20 Q10 14 15 9Z"/><path d="M12 20 H32 M11 28 H33" stroke="#e6e6e6" stroke-width="2"/></svg>
    Visit the ancient heritage of humanity</div>
  <div class="abs tile" style="left:606px;top:1923px">
    <svg viewBox="0 0 44 44"><circle cx="11" cy="30" r="7" fill="none" stroke="#333" stroke-width="2.5"/><circle cx="33" cy="30" r="7" fill="none" stroke="#333" stroke-width="2.5"/><circle cx="26" cy="8" r="3"/><path d="M11 30 L19 20 L26 24 L33 30 M19 20 L24 14 L30 20" stroke="#333" stroke-width="2.5" fill="none"/></svg>
    Make some aquatic sport</div>
  <div class="abs tile" style="left:837px;top:1923px">
    <svg viewBox="0 0 44 44"><circle cx="32" cy="10" r="5"/><path d="M6 22 L18 10 L24 16 L14 24Z"/><path d="M2 28 Q7 24 12 28 T22 28 T32 28 T42 28 M2 35 Q7 31 12 35 T22 35 T32 35 T42 35" stroke="#333" stroke-width="3" fill="none"/></svg>
    Enjoy the pool</div>

  <!-- philosophy -->
  <div class="abs philo-band" role="img" aria-label="Photo of rocky islets in a turquoise Ibiza bay under a cloudy sky"></div>
  <h2 class="abs philo-title serif" style="font-weight:400">Our Philosophy</h2>
  <p class="abs philo-text">Maecenas vel tortor accumsan quam varius imperdiet vel eget elit. Aenean facilisis tincidunt lectus, id dictum nisi luctus eget. Vivamus efficitur ex condimentum, malesuada eros eget, feugiat nibh. Sed tellus ex, imperdiet eget gravida sit amet, volutpat eget turpis. In nec ultricies est. Etiam mattis augue vehicula odio posuere, sit amet tempus lectus luctus.</p>

  <!-- experiences -->
  <h2 class="abs section-title serif" style="top:2700px;font-weight:400">Experiences</h2>
  <div class="abs exp-photo" role="img" aria-label="Video still of a smiling guest in a sun hat in a flowering garden"></div>
  <div class="abs exp-play"></div>
  <svg class="abs" style="left:365px;top:2884px" width="17" height="20" viewBox="0 0 17 20"><path d="M2 1 L16 10 L2 19Z" fill="#222"/></svg>
  <div class="abs exp-panel"></div>
  <p class="abs exp-quote">The house is great. It's quiet at night and the pool gets sun all day. There are 5 bedrooms but only one has an actual AC unit - the rest are fans. Wi-Fi works really well. Pool is big. Kitchen well stocked and enough plates / cutlery / dish washer etc. There is a hypermarket less than 1km away by foot which sells food, alcohol and other things you may need.</p>
  <div class="abs exp-ref">Can Roure.. Puig Alt. ET-0000-X</div>
  <div class="abs avatar" role="img" aria-label="Guest portrait"></div>
  <div class="abs exp-name">Marta</div>
  <svg class="abs quote-mark" viewBox="0 0 92 80"><path d="M0 40 Q0 6 34 0 V14 Q18 18 18 34 H38 V80 H0Z M52 40 Q52 6 86 0 V14 Q70 18 70 34 H92 V80 H52Z" fill="#bdbdbd"/></svg>
  <svg class="abs exp-arrow" style="left:52px" viewBox="0 0 22 28"><path d="M15 4 L6 14 L15 24" stroke="#666" stroke-width="3" fill="none"/></svg>
  <svg class="abs exp-arrow" style="left:1125px" viewBox="0 0 22 28"><path d="M7 4 L16 14 L7 24" stroke="#666" stroke-width="3" fill="none"/></svg>

  <!-- properties -->
  <div class="abs props-band"></div>
  <h2 class="abs section-title serif" style="top:3185px;font-weight:400">Propertise</h2>

  <div class="abs prop-photo" style="left:143px;background:linear-gradient(160deg,#a0532c 0%,#e8dcc8 40%,#c7a57e 70%,#6b4a2e 100%)" role="img" aria-label="Photo of a rustic living room with sofas and wooden beams"></div>
  <div class="abs prop-photo" style="left:451px;background:linear-gradient(180deg,#2d6fd0 0%,#7fb0e0 35%,#3f7a3a 55%,#1d8fe0 78%,#0f5fb5 100%)" role="img" aria-label="Photo of a villa swimming pool surrounded by palms and cacti"></div>
  <div class="abs prop-photo" style="left:758px;background:linear-gradient(180deg,#2a5cc4 0%,#6d9ad8 40%,#4a7a3a 65%,#e0e0e0 85%,#8a8a8a 100%)" role="img" aria-label="Photo of white sun loungers on a pool terrace with a bottle on a table"></div>

  <div class="abs prop-name" style="left:145px">Agroturismo Can Serra</div>
  <div class="abs prop-name" style="left:452px">Villa Can Bosc</div>
  <div class="abs prop-name" style="left:759px">Villa Can Pla</div>

  <div class="abs prop-meta" style="left:145px"><span>&#9679; Sant Carles</span><span>&#9776; See file</span></div>
  <div class="abs prop-meta" style="left:452px"><span>&#9679; San Jose</span><span>&#9776; See file</span></div>
  <div class="abs prop-meta" style="left:759px"><span>&#9679; Santa Eulalia</span><span>&#9776; See file</span></div>

  <div class="abs prop-note" style="left:145px">The best price, guaranteed<br>Immediate confirmation</div>
  <div class="abs prop-note" style="left:452px">The best price, guaranteed<br>Immediate confirmation</div>
  <div class="abs prop-note" style="left:759px">The best price, guaranteed<br>Immediate confirmation</div>

  <div class="btn view-all">VIEW ALL</div>

  <!-- newsletter -->
  <h2 class="abs section-title serif" style="top:3747px;font-weight:400">Newsletter Sign Up</h2>
  <div class="abs email">Email Address</div>
  <div class="btn submit">SUBMIT</div>

  <!-- footer -->
  <svg class="abs" style="left:0;top:3900px" width="1200" height="204" viewBox="0 0 1200 204">
    <defs>
      <linearGradient id="footWave" x1="0" x2="1" y1="0" y2="0">
        <stop offset="0" stop-color="#6b9a2a"/>
        <stop offset="0.55" stop-color="#3a9a7a"/>
        <stop offset="1" stop-color="#2f86c7"/>
      </linearGradient>
    </defs>
    <path d="M0 15 Q300 110 620 40 Q900 -10 1200 60 L1200 204 L0 204Z" fill="url(#footWave)"/>
    <path d="M0 30 Q320 125 640 55 Q920 5 1200 80 L1200 204 L0 204Z" fill="#1d1d1d"/>
  </svg>
  <div class="abs foot-links"><span>Home</span><span>|</span><span>All Properties</span><span>|</span><span>Experience</span><span>|</span><span>About us</span><span>|</span><span>Contact Us</span><span>|</span><span>Book Now</span></div>
  <div class="abs copyright">Copyright &copy; 2019 &nbsp;Amber &amp; Slate Ibiza. &nbsp;All rights reserved.</div>
  <div class="abs socials"><span></span><span></span><span></span><span></span></div>

</div>
</body>
</html>
```